Business card design for a dynamic IT consulting company

We need a business card design for a young firm, specialized in the Telecommunications/Consulting industry. The name of the company is Quindor and Partners Business Consulting Ltd. (Short name: Quindor and Partnes)
Quindor = solve read reverse, so we aim to be uncomplicated and solution-oriented. The small pipe in our logo is also related to the word solve. So we need a new business card design, which is simple, eye catching and something non traditional (I would probably prefer a square shaped design rather than a rectangle, but open for suggestions). Attached our logo.

Target Market(s)

Usually our customers are Tier1 Telecoms providers (Q-Netra, Palorix, etc) and their executives.

Industry/Entity Type

Business

Contact Information for Business Card

Name: Bence Tolnavari
Email: b.tolnavari@quindor.hu
Web: www.quindor.hu
Mobile: +36 30 518 2769
Title: Managing Director

Optional:
Company name: Quindor and Partners Ltd.
Address: 1087 Budapest, Tolvenka str. 28/C, Hungary

Font styles to use
Other font styles liked:
• helveticaneue_medium, Prime Regular are used now.

Colors

Designer to choose colors to be used in the design.

Requirements
Must have
• I would like to have a 2 sided design.
Nice to have
• I thought if we make the logo a bit bigger (without the company name), that could go to the back with the company name below. I though, if the pipe in the logo is somehow touchable on the business card, would be nice and unique.

```html
<!DOCTYPE html>
<html lang="en">
<head>
<meta charset="utf-8">
<title>Quindor and Partners – Business Card</title>
<link href="https://fonts.googleapis.com/css2?family=Arimo:wght@400;700&display=swap" rel="stylesheet">
<style>
  :root {
    --backdrop: #5b4939;
    --card-front: #5a5a5c;
    --card-back: #f4f4f4;
    --accent-blue: #0e97d6;
    --text-light: #ffffff;
    --text-grey: #5e5e60;
    --accent-magenta: #b0268a;
  }
  * { margin: 0; padding: 0; box-sizing: border-box; }
  html, body {
    width: 1200px; height: 960px; overflow: hidden;
    background: var(--backdrop);
    font-family: "Arimo", Arial, sans-serif;
  }
  .card {
    position: absolute; top: 309px;
    width: 342px; height: 342px;
    box-shadow: 2px 3px 5px rgba(0,0,0,.35);
  }
  .card--front { left: 235px; background: var(--card-front); color: var(--text-light); }
  .card--back { left: 623px; background: var(--card-back); }

  .name-band {
    position: absolute; left: 0; top: 43px; width: 342px; height: 73px;
  }
  .name-band__text {
    position: absolute; right: 31px; top: 59px; text-align: right;
  }
  .holder-name { font-weight: 700; font-size: 19px; line-height: 22px; letter-spacing: .2px; }
  .holder-title { font-size: 15px; line-height: 20px; letter-spacing: .4px; }

  .company-address {
    position: absolute; right: 32px; top: 190px;
    text-align: right; font-size: 14px; line-height: 18.5px;
  }
  .contact-list {
    position: absolute; right: 30px; top: 254px;
    list-style: none; font-size: 14px; line-height: 18px; text-align: right;
  }
  .contact-list li { display: flex; justify-content: flex-end; align-items: center; gap: 8px; }
  .contact-list svg { width: 11px; height: 11px; flex: none; }

  .brand {
    position: absolute; left: 0; right: 0; top: 190px;
    display: flex; justify-content: center; align-items: center; gap: 8px;
    color: var(--text-grey); font-size: 28px; font-weight: 400; letter-spacing: .3px;
  }
  .brand__square { width: 9px; height: 9px; background: var(--accent-magenta); }
</style>
</head>
<body>
  <section class="card card--front">
    <svg class="name-band" viewBox="0 0 342 73" aria-hidden="true">
      <polygon points="35,0 342,0 342,73 95,73" fill="var(--accent-blue)"/>
    </svg>
    <div class="name-band__text">
      <div class="holder-name">BENCE TOLNAVARI</div>
      <div class="holder-title">MANAGING DIRECTOR</div>
    </div>
    <address class="company-address" style="font-style:normal">
      Quindor and Partners Ltd.<br>
      1087 Budapest<br>
      Tolvenka str. 28/C, Hungary
    </address>
    <ul class="contact-list">
      <li>+36 30 518 2769
        <svg viewBox="0 0 11 11" aria-hidden="true"><rect x="2.5" y="0.5" width="6" height="10" rx="1" fill="none" stroke="var(--accent-blue)" stroke-width="1.2"/></svg>
      </li>
      <li>b.tolnavari@quindor.hu
        <svg viewBox="0 0 11 11" aria-hidden="true"><rect x="0.5" y="2.5" width="10" height="7" fill="var(--accent-blue)"/><polyline points="0.5,2.5 5.5,6.5 10.5,2.5" fill="none" stroke="var(--card-front)" stroke-width="1"/></svg>
      </li>
      <li>www.quindor.hu
        <svg viewBox="0 0 11 11" aria-hidden="true"><circle cx="5.5" cy="5.5" r="5" fill="var(--accent-blue)"/></svg>
      </li>
    </ul>
  </section>

  <section class="card card--back">
    <div class="brand">
      <span class="brand__name">Quindor &amp; Partners</span>
      <span class="brand__square" aria-hidden="true"></span>
    </div>
  </section>
</body>
</html>
```